Seeking funky, innovative business cards

I am looking to refresh our current business cards to something more engaging, visual and impactful. We are a management consultancy firm, see website (www.larkstone-partners.com.au). I've included our colour scheme, sample of the slides we use and our old business cards. We would like our cards to have icons. The card should display:- Name- Title- Mobile number- Address- Email address- Website - Company logo- Our purpose statement "we shape workplaces people are glad to join"

Contact Information for Business Card

Brennan Ulfsson
Consultant
0468 927 341
Level 3, 218 Wexley Street, Melbourne 3000
brennan@larkstone-partners.com.au
www.larkstone-partners.com.au

Purpose statement "we shape workplaces people are glad to join"
LOGO available in google images

Font styles to use
Other font styles liked:
• Open Sans Light, Bebas Neue (open to other cool foints)

Colors
ffc214
5c5c5c
f5f5f5
fefefe

Requirements
Must have
• - Name
• - Title
• - Mobile number
• - Address
• - Email address
• - Website
• - Company logo
• - Our purpose statement "we shape workplaces people are glad to join"
Nice to have
• - Icons
• - Colour (see our colour scheme"

```html
<!DOCTYPE html>
<html lang="en">
<head>
<meta charset="utf-8">
<title>Larkstone Partners – Business Card</title>
<link rel="stylesheet" href="https://fonts.googleapis.com/css2?family=Roboto:ital,wght@0,300;0,400;0,500;1,400&display=swap">
<style>
  :root {
    --backdrop: #c4c4c4;
    --card: #ffffff;
    --accent: #f7a823;
    --accent-yellow: #ffc214;
    --ink: #5c5c5c;
    --ink-dark: #3a3a3a;
    --logo-ink: #474c4c;
  }
  * { margin: 0; padding: 0; box-sizing: border-box; }
  html, body {
    width: 1200px; height: 1200px; overflow: hidden;
    background: var(--backdrop);
    font-family: "Roboto", Arial, sans-serif;
  }
  .card {
    position: absolute; left: 218px; width: 800px; height: 457px;
    background: var(--card);
  }
  .card--front { top: 115px; }
  .card--back { top: 638px; }

  .identity { position: absolute; left: 54px; top: 50px; display: flex; align-items: center; }
  .identity__dot { width: 22px; height: 22px; border-radius: 50%; background: var(--accent-yellow); }
  .identity__text { margin-left: 87px; }
  .identity__name { font-size: 30px; font-weight: 400; color: var(--accent); line-height: 1; }
  .identity__title { font-size: 20px; font-weight: 500; color: var(--ink-dark); margin-top: 4px; line-height: 1.2; }

  .address {
    position: absolute; right: 55px; top: 270px;
    text-align: right; font-size: 19px; color: var(--ink); line-height: 24px; font-weight: 400;
  }
  .contacts { position: absolute; right: 55px; top: 333px; list-style: none; }
  .contacts li {
    display: flex; justify-content: flex-end; align-items: center; gap: 16px;
    font-size: 19px; color: var(--ink); line-height: 25.5px;
  }
  .contacts svg { width: 19px; height: 19px; flex: none; }

  .brand {
    position: absolute; left: 0; right: 0; top: 205px;
    display: flex; justify-content: center; align-items: center; gap: 18px;
  }
  .brand__dot { width: 26px; height: 26px; border-radius: 50%; background: var(--accent-yellow); }
  .brand__name { font-size: 60px; font-weight: 400; color: var(--logo-ink); letter-spacing: -1px; line-height: 1; }

  .purpose {
    position: absolute; left: 0; right: 0; top: 382px;
    text-align: center; font-size: 21px; font-style: italic; color: var(--ink-dark);
  }
  .purpose__highlight { color: var(--accent); }
</style>
</head>
<body>
  <section class="card card--front">
    <div class="identity">
      <span class="identity__dot"></span>
      <div class="identity__text">
        <p class="identity__name">Brennan Ulfsson</p>
        <p class="identity__title">Consultant</p>
      </div>
    </div>

    <p class="address">Level 3, 218 Wexley Street,<br>Melbourne 3000</p>

    <ul class="contacts">
      <li>0468 927 341
        <svg viewBox="0 0 20 20" aria-hidden="true"><path fill="#f7a823" d="M5 2l3 4-2 2c1 2 3 4 5 5l2-2 4 3-2 3C9 17 3 11 2 5z"/></svg>
      </li>
      <li>brennan@larkstone-partners.com.au
        <svg viewBox="0 0 20 20" aria-hidden="true"><rect x="2" y="5" width="16" height="11" fill="#f7a823"/><path d="M2 5l8 6 8-6" fill="none" stroke="#fff" stroke-width="1.5"/></svg>
      </li>
      <li>www.larkstone-partners.com.au
        <svg viewBox="0 0 20 20" aria-hidden="true"><circle cx="10" cy="10" r="8.5" fill="#f7a823"/><circle cx="10" cy="10" r="5" fill="none" stroke="#fff" stroke-width="1.4"/><path d="M5 10h10M10 5v10" stroke="#fff" stroke-width="1.4"/></svg>
      </li>
    </ul>
  </section>

  <section class="card card--back">
    <div class="brand">
      <span class="brand__dot"></span>
      <span class="brand__name">Larkstone Partners</span>
    </div>
    <p class="purpose">we shape workplaces people <span class="purpose__highlight">are glad to join</span></p>
  </section>
</body>
</html>
```